hi
would like the design about the some. just with our  details and logo
office number 01632960482
Mobil number 07700900317
web tidalbroom.ltd
email tidalbroom@postnest.co.uk
on the back we would like to put a price list

```html
<!DOCTYPE html>
<html lang="en">
<head>
<meta charset="utf-8">
<title>Tidalbroom Cleaning &amp; Maintenance – Flyer</title>
<link rel="stylesheet" href="https://fonts.googleapis.com/css2?family=Poppins:ital,wght@0,400;0,500;0,600;0,700;0,800;1,500&family=Bebas+Neue&family=Oswald:wght@500;600&display=swap">
<style>
:root{
  --blue:#1f6bbd;
  --blue-dark:#1a4f96;
  --navy:#2b3391;
  --pink:#ee4fb4;
  --pink-soft:#f58ad0;
  --ink:#222;
  --stage:#ffffff;
  --white:#fff;
}
*{box-sizing:border-box;margin:0;padding:0}
html,body{width:826px;height:1200px;overflow:hidden;background:var(--stage)}
body{font-family:"Poppins",sans-serif;position:relative}
.flyer{position:absolute;width:640px;height:828px;background:var(--white);overflow:hidden;
  transform-origin:0 0;transform:scale(.594);box-shadow:0 10px 30px rgba(0,0,0,.25)}
.flyer--front{left:22px;top:354px}
.flyer--back{left:424px;top:354px}
.flyer svg.art{position:absolute;left:0;top:0;width:640px;height:828px}
.abs{position:absolute}
.brand{position:absolute;text-align:center;color:var(--blue);font-weight:700;line-height:1;white-space:nowrap}
.brand__name{font-size:30px;letter-spacing:0}
.brand__tag{font-size:10px;margin-top:4px}
.pill{position:absolute;left:0;height:40px;padding:0 22px 0 38px;border-radius:0 22px 22px 0;
  background:linear-gradient(#fafafa,#cfcfcf);font-weight:700;font-size:21px;color:var(--ink);
  display:flex;align-items:center;box-shadow:0 2px 4px rgba(0,0,0,.3)}
.about{left:38px;top:412px;width:252px;font-size:9.3px;line-height:1.2;color:var(--white)}
.about p+p{margin-top:10px}
.services{left:38px;top:614px;list-style:none;color:var(--white);font-size:11px;line-height:17px}
.services li{display:flex;align-items:center;gap:7px}
.tick{width:10px;height:10px}
.headline{left:322px;top:356px;width:300px;font-family:"Bebas Neue",sans-serif;color:var(--blue);
  font-size:47px;line-height:43px;text-align:center;letter-spacing:.3px;font-weight:400}
.subline{left:325px;top:452px;width:300px;font-style:italic;font-weight:500;font-size:13.6px;line-height:19px;color:var(--ink)}
.quote-bar{left:343px;top:494px;width:297px;height:40px;background:var(--blue);color:var(--white);
  font-family:"Bebas Neue",sans-serif;font-size:22px;display:flex;align-items:center;padding-left:16px;border-radius:18px 0 0 18px}
.contacts{left:363px;top:548px;list-style:none;font-size:13.5px;color:var(--ink)}
.contacts li{display:flex;align-items:center;gap:12px;height:27px}
.contacts b{color:var(--blue);font-weight:500}
.contacts svg{width:20px;height:20px}
.follow{left:395px;top:656px;font-size:13px;display:flex;align-items:center;gap:6px;color:var(--ink)}
.follow i{display:inline-block;width:19px;height:19px;background:var(--blue);border-radius:3px}
.follow span{margin-right:6px}
.footer-note{left:0;width:640px;text-align:center;color:var(--white);font-size:17.5px;line-height:21px}
.footer-note .lead{color:var(--pink-soft)}
.section-title{left:0;width:640px;text-align:center;color:var(--blue);font-weight:700;font-size:23px}
.price-card{position:absolute;width:103px;height:123px;background:var(--white);border-radius:6px;
  box-shadow:0 2px 6px rgba(0,0,0,.25);overflow:hidden;text-align:center}
.price-card__head{background:linear-gradient(var(--blue),var(--blue-dark));color:var(--white);height:50px;padding-top:4px}
.price-card__name{font-family:"Oswald",sans-serif;font-size:9px;font-weight:500;line-height:11px}
.price-card__from{font-size:5px;line-height:5px}
.price-card__price{font-weight:700;font-size:17px;line-height:19px}
.price-card__unit{font-size:5px;line-height:5px}
.price-card ul{list-style:none;text-align:left;font-size:7.2px;line-height:10px;color:var(--ink);padding:4px 8px 0}
.price-card .btn{display:inline-block;margin-top:4px;background:var(--pink);color:var(--white);font-size:6px;
  font-weight:600;padding:1px 10px;border-radius:6px}
.price-card--wide{width:122px;height:140px}
.price-card--wide .price-card__head{height:58px;padding-top:6px}
.price-card--wide .price-card__price{font-size:19px}
.price-card--wide ul{padding:12px 10px 0;min-height:62px}
.other-frame{left:73px;top:503px;width:494px;height:178px;border:1.5px solid #cfcfcf;border-radius:16px}
</style>
</head>
<body>

<!-- FRONT -->
<section class="flyer flyer--front" aria-label="Front of flyer">
  <svg class="art" viewBox="0 0 640 828">
    <defs>
      <linearGradient id="photoA" x1="0" y1="0" x2="1" y2="1">
        <stop offset="0" stop-color="#c9d3dc"/><stop offset=".45" stop-color="#8d5a45"/><stop offset="1" stop-color="#5c6a3e"/>
      </linearGradient>
      <linearGradient id="panel" x1="0" y1="0" x2="0" y2="1">
        <stop offset="0" stop-color="#1e67b8"/><stop offset="1" stop-color="#1d5fae"/>
      </linearGradient>
      <linearGradient id="pinkFadeA" x1="175" y1="0" x2="640" y2="0" gradientUnits="userSpaceOnUse">
        <stop offset=".35" stop-color="#ee4fb4" stop-opacity="0"/><stop offset=".7" stop-color="#ee4fb4"/>
      </linearGradient>
    </defs>
    <rect role="img" aria-label="Photo of a brick building with a conservatory and a cleaner using a water-fed pole on the windows" x="0" y="0" width="640" height="340" fill="url(#photoA)"/>
    <path d="M140,0 C250,135 470,165 640,105 L640,0Z" fill="var(--blue)"/>
    <path d="M175,6 C285,121 480,146 640,86" fill="none" stroke="url(#pinkFadeA)" stroke-width="10"/>
    <path d="M175,0 C285,115 480,140 640,80 L640,0Z" fill="var(--white)"/>
    <path d="M0,335 L275,335 C330,420 330,600 322,720 L0,720Z" fill="url(#panel)"/>
    <path d="M0,340 C220,318 450,305 640,290 L640,340 L0,340Z" fill="var(--white)"/>
    <path d="M150,335 C300,320 470,302 640,285 L640,300 C470,316 300,334 160,345Z" fill="var(--pink-soft)"/>
    <circle role="img" aria-label="Inset photo of a service van parked outside a building" cx="87" cy="251" r="85" fill="#7c8a9a" stroke="#1d1d1d" stroke-width="5"/>
    <path d="M0,770 C200,690 440,685 640,745 L640,828 L0,828Z" fill="var(--navy)"/>
    <path d="M0,764 C200,684 440,679 640,739" fill="none" stroke="var(--pink)" stroke-width="9"/>
  </svg>

  <div class="brand" style="left:325px;top:40px;width:190px">
    <div class="brand__name">TIDALBROOM</div>
    <div class="brand__tag">CLEANING &amp; MAINTENANCE LTD</div>
  </div>

  <div class="pill" style="top:363px">ABOUT US</div>
  <div class="abs about">
    <p>Tidalbroom Cleaning Ltd have been cleaning windows for commercial and residential properties throughout Hutton, Shenfield and the surrounding areas since 1999. We cover most towns in Essex including Brentwood, Chelmsford, Romford, Loughton and Billericay.</p>
    <p>When it comes to window cleaning, we believe in giving our clients the best possible service and that is why we were the first window cleaning business in Brentwood to use the Pure Water Fed Pole Systems, alongside traditional ladders and hand tools.</p>
  </div>

  <div class="pill" style="top:557px">OUR SERVICES</div>
  <ul class="abs services">
    <li><svg class="tick" viewBox="0 0 10 10"><circle cx="5" cy="5" r="5" fill="#fff"/><path d="M2.6,5.2 4.3,6.8 7.4,3.4" stroke="#1f6bbd" stroke-width="1.4" fill="none"/></svg>Window cleaning</li>
    <li><svg class="tick" viewBox="0 0 10 10"><circle cx="5" cy="5" r="5" fill="#fff"/><path d="M2.6,5.2 4.3,6.8 7.4,3.4" stroke="#1f6bbd" stroke-width="1.4" fill="none"/></svg>Conservatory cleaning</li>
    <li><svg class="tick" viewBox="0 0 10 10"><circle cx="5" cy="5" r="5" fill="#fff"/><path d="M2.6,5.2 4.3,6.8 7.4,3.4" stroke="#1f6bbd" stroke-width="1.4" fill="none"/></svg>Pressure washing</li>
    <li><svg class="tick" viewBox="0 0 10 10"><circle cx="5" cy="5" r="5" fill="#fff"/><path d="M2.6,5.2 4.3,6.8 7.4,3.4" stroke="#1f6bbd" stroke-width="1.4" fill="none"/></svg>Gutter cleaning</li>
    <li><svg class="tick" viewBox="0 0 10 10"><circle cx="5" cy="5" r="5" fill="#fff"/><path d="M2.6,5.2 4.3,6.8 7.4,3.4" stroke="#1f6bbd" stroke-width="1.4" fill="none"/></svg>Soffit's &amp; fascia cleaning</li>
  </ul>

  <h1 class="abs headline">RELIABLE WINDOW<br>CLEANING SERVICES</h1>
  <p class="abs subline">FOR RESIDENTIAL AND COMMERCIAL CUSTOMERS IN AND AROUND ESSEX</p>
  <div class="abs quote-bar">FOR A FREE QUOTE PLEASE CONTACT US:</div>
  <ul class="abs contacts">
    <li><svg viewBox="0 0 20 20"><circle cx="10" cy="10" r="8.6" fill="none" stroke="#222" stroke-width="1.6"/><path d="M7,5.5 8.6,7.6 7.8,8.8 C8.5,10.4 9.6,11.5 11.2,12.2 L12.4,11.4 14.5,13 13.4,14.6 C9.5,14.4 5.6,10.5 5.4,6.6Z" fill="#222"/></svg><span><b>Office:</b> 01632960482</span></li>
    <li><svg viewBox="0 0 20 20"><circle cx="10" cy="10" r="8.6" fill="none" stroke="#222" stroke-width="1.6"/><path d="M7,5.5 8.6,7.6 7.8,8.8 C8.5,10.4 9.6,11.5 11.2,12.2 L12.4,11.4 14.5,13 13.4,14.6 C9.5,14.4 5.6,10.5 5.4,6.6Z" fill="#222"/></svg><span><b>Mobile:</b> 07700900317</span></li>
    <li><svg viewBox="0 0 20 20"><circle cx="10" cy="10" r="7" fill="none" stroke="#222" stroke-width="1.6"/><path d="M3,10H17M10,3C6,7 6,13 10,17M10,3C14,7 14,13 10,17" fill="none" stroke="#222" stroke-width="1.3"/></svg><span>web tidalbroom.ltd</span></li>
    <li><svg viewBox="0 0 20 20"><rect x="3" y="5.5" width="14" height="9.5" fill="#222"/><path d="M3,5.5 10,11 17,5.5" fill="none" stroke="#fff" stroke-width="1.2"/></svg><span>tidalbroom@postnest.co.uk</span></li>
  </ul>
  <div class="abs follow"><span>Follow Us On</span><i></i><i></i><i></i></div>

  <p class="abs footer-note" style="top:718px"><span class="lead">Use 'Contact Us' Form</span><br>on our web site &amp; add images of your property,<br>we will then provide a quote with-in 48 Hours.</p>
</section>

<!-- BACK -->
<section class="flyer flyer--back" aria-label="Back of flyer with price list">
  <svg class="art" viewBox="0 0 640 828">
    <defs>
      <linearGradient id="photoB" x1="0" y1="0" x2="1" y2="0">
        <stop offset="0" stop-color="#9a9a9a"/><stop offset=".45" stop-color="#4e5560"/><stop offset="1" stop-color="#8fa27a"/>
      </linearGradient>
      <linearGradient id="pinkFadeB" x1="205" y1="0" x2="640" y2="0" gradientUnits="userSpaceOnUse">
        <stop offset=".35" stop-color="#ee4fb4" stop-opacity="0"/><stop offset=".7" stop-color="#ee4fb4"/>
      </linearGradient>
    </defs>
    <rect role="img" aria-label="Photo of a window cleaner in a cap using a squeegee on a window" x="0" y="0" width="640" height="300" fill="url(#photoB)"/>
    <path d="M170,0 C270,118 470,148 640,92 L640,0Z" fill="var(--blue)"/>
    <path d="M205,6 C300,106 480,131 640,76" fill="none" stroke="url(#pinkFadeB)" stroke-width="10"/>
    <path d="M205,0 C300,100 480,125 640,70 L640,0Z" fill="var(--white)"/>
    <path d="M0,248 C220,275 450,268 640,228 L640,828 L0,828Z" fill="var(--white)"/>
    <path d="M0,244 C220,270 450,262 640,222 L640,238 C450,282 220,290 0,258Z" fill="var(--pink-soft)"/>
    <path d="M0,772 C200,692 440,687 640,747 L640,828 L0,828Z" fill="var(--navy)"/>
    <path d="M0,766 C200,686 440,681 640,741" fill="none" stroke="var(--pink)" stroke-width="9"/>
  </svg>

  <div class="brand" style="left:365px;top:40px;width:142px">
    <div class="brand__name" style="font-size:22px">TIDALBROOM</div>
    <div class="brand__tag" style="font-size:7.5px;margin-top:3px">CLEANING &amp; MAINTENANCE LTD</div>
  </div>

  <h2 class="abs section-title" style="top:305px">RELIABLE WINDOW CLEANING SERVICE</h2>

  <div class="price-card" style="left:37px;top:345px"><div class="price-card__head"><div class="price-card__name">SEMI DETACHED (3/4 BED)</div><div class="price-card__price">£14</div><div class="price-card__unit">PER VISIT</div></div><ul><li>Conservatory roofs from £60.00</li><li>+ Drives from £120.00</li><li>+ Gutters from £60.00</li></ul><span class="btn">BOOK NOW</span></div>
  <div class="price-card" style="left:151px;top:345px"><div class="price-card__head"><div class="price-card__name">DETACHED (3/4 BED)</div><div class="price-card__price">£16</div><div class="price-card__unit">PER VISIT</div></div><ul><li>+ Conservatory roofs from £60.00</li><li>+ Drives from £120.00</li><li>+ Gutters from £60.00</li></ul><span class="btn">BOOK NOW</span></div>
  <div class="price-card" style="left:265px;top:345px"><div class="price-card__head"><div class="price-card__name">DETACHED (5 BED)</div><div class="price-card__price">£23</div><div class="price-card__unit">PER VISIT</div></div><ul><li>+ Conservatory roofs from £60.00</li><li>+ Drives from £120.00</li><li>+ Gutters from £60.00</li></ul><span class="btn">BOOK NOW</span></div>
  <div class="price-card" style="left:379px;top:345px"><div class="price-card__head"><div class="price-card__name">TERRACE (FRONT ONLY)</div><div class="price-card__price">£10</div><div class="price-card__unit">PER VISIT</div></div><ul><li>+ Conservatory roofs from £60.00</li><li>+ Drives from £120.00</li><li>+ Gutters from £60.00</li></ul><span class="btn">BOOK NOW</span></div>
  <div class="price-card" style="left:493px;top:345px"><div class="price-card__head"><div class="price-card__name">TERRACE (FRONT AND BACK)</div><div class="price-card__price">£14</div><div class="price-card__unit">PER VISIT</div></div><ul><li>+ Conservatory roofs from £60.00</li><li>+ Drives from £120.00</li><li>+ Gutters from £60.00</li></ul><span class="btn">BOOK NOW</span></div>

  <div class="abs other-frame"></div>
  <h2 class="abs section-title" style="top:484px"><span style="background:#fff;padding:0 8px">OTHER CLEANING SERVICES</span></h2>

  <div class="price-card price-card--wide" style="left:102px;top:521px"><div class="price-card__head"><div class="price-card__name">CONSERVATORY ROOF CLEANING</div><div class="price-card__from">FROM</div><div class="price-card__price">£60</div><div class="price-card__unit">PER VISIT</div></div><ul><li>+ Drives from £120.00</li><li>+ Gutters from £60.00</li></ul><span class="btn">GET A QUOTE</span></div>
  <div class="price-card price-card--wide" style="left:259px;top:521px"><div class="price-card__head"><div class="price-card__name">DRIVEWAYS &amp; PATIO CLEANING</div><div class="price-card__from">FROM</div><div class="price-card__price">£120</div><div class="price-card__unit">PER VISIT</div></div><ul><li>+ Conservatory roofs from £60.00</li><li>+ Gutters from £60.00</li></ul><span class="btn">GET A QUOTE</span></div>
  <div class="price-card price-card--wide" style="left:418px;top:521px"><div class="price-card__head"><div class="price-card__name">GUTTER CLEANING</div><div class="price-card__from">FROM</div><div class="price-card__price">£60</div><div class="price-card__unit">PER VISIT</div></div><ul><li>+ Conservatory roofs from £60.00</li><li>+ Drives from £120.00</li></ul><span class="btn">GET A QUOTE</span></div>

  <p class="abs footer-note" style="top:720px"><span class="lead">Use 'Contact Us' Form</span><br>on our web site &amp; add images of your property,<br>we will then provide a quote with-in 48 Hours.</p>
</section>

</body>
</html>
```